Corporate Business Card

Very professional, Modern, Not to busy, include phone address email, website
(253) 617-4930, 18761 52nd Avenue S, Kent, WA 98047, martin@plumlinegroup.com, varkoworks.com

Target Market(s)

Manufacturing

Industry/Entity Type

Aero, machining, manufacturing, Off road racing

Contact Information for Business Card

Phone, address email, website

```html
<!DOCTYPE html>
<html lang="en">
<head>
<meta charset="utf-8">
<title>Varko Works – Business Card</title>
<link rel="stylesheet" href="https://fonts.googleapis.com/css2?family=Roboto:wght@400&family=Saira:wght@600;700&display=swap">
<style>
  :root {
    --stage: #2a2a2a;
    --navy: #293766;
    --red: #c0272d;
    --paper: #ececec;
    --white: #f2f2f2;
    --ink: #2a3668;
  }
  html, body {
    margin: 0;
    width: 1200px;
    height: 1138px;
    overflow: hidden;
    background: var(--stage);
  }
  .card {
    position: absolute;
    border-radius: 16px;
    overflow: hidden;
  }
  .card-front {
    left: 274px; top: 186px;
    width: 623px; height: 376px;
    background: var(--navy);
  }
  .front-brand {
    position: absolute;
    left: 0; right: 0; top: 132px;
    text-align: center;
    font-family: "Saira", sans-serif;
    font-weight: 700;
    font-size: 62px;
    letter-spacing: 2px;
    color: var(--white);
    line-height: 1;
  }
  .front-web {
    position: absolute;
    left: 0; right: 0; top: 326px;
    text-align: center;
    font-family: "Roboto", sans-serif;
    font-size: 15px;
    letter-spacing: 9px;
    color: var(--white);
  }
  .front-web .accent { color: var(--red); }

  .card-back {
    left: 276px; top: 608px;
    width: 618px; height: 374px;
    background: var(--paper);
  }
  .back-panel {
    position: absolute;
    left: 0; top: 0;
    width: 618px; height: 374px;
  }
  .back-brand {
    position: absolute;
    left: 524px; top: 187px;
    transform: translate(-50%, -50%) rotate(-90deg);
    white-space: nowrap;
    font-family: "Saira", sans-serif;
    font-weight: 700;
    font-size: 40px;
    letter-spacing: 1px;
    color: var(--white);
    line-height: 1;
  }
  .contact {
    position: absolute;
    left: 68px; top: 106px;
  }
  .contact-name {
    margin: 0 0 14px;
    font-family: "Saira", sans-serif;
    font-weight: 700;
    font-size: 28px;
    line-height: 1;
    color: var(--ink);
  }
  .contact-name .surname { color: var(--red); }
  .contact-list {
    list-style: none;
    margin: 0; padding: 0;
    font-family: "Roboto", sans-serif;
    font-size: 16.5px;
    color: var(--ink);
  }
  .contact-list li {
    position: relative;
    padding-left: 31px;
    line-height: 24px;
  }
  .contact-list svg {
    position: absolute;
    left: 0; top: 5px;
    width: 14px; height: 14px;
    fill: var(--red);
  }
</style>
</head>
<body>

<section class="card card-front">
  <div class="front-brand">VARKO WORKS</div>
  <div class="front-web">www.varko<span class="accent">works</span>.com</div>
</section>

<section class="card card-back">
  <svg class="back-panel" viewBox="0 0 618 374" aria-hidden="true">
    <path d="M460 0 Q336 200 464 374 L618 374 L618 0 Z" fill="var(--red)"/>
    <path d="M466 0 Q346 200 474 374 L618 374 L618 0 Z" fill="var(--navy)"/>
  </svg>
  <div class="back-brand">VARKO WORKS</div>

  <div class="contact">
    <h1 class="contact-name">MARTIN <span class="surname">HALE</span></h1>
    <ul class="contact-list">
      <li>
        <svg viewBox="0 0 16 16"><path d="M1 6c0-2 3-3 7-3s7 1 7 3v1h-4V5.5H5V7H1z M3 8h10l1 6H2z"/></svg>
        (253) 617-4930
      </li>
      <li>
        <svg viewBox="0 0 16 16"><path d="M1 3h14v10H1z M2 4.2v.6l6 4.4 6-4.4v-.6L8 8.2z" fill-rule="evenodd"/></svg>
        martin@plumlinegroup.com
      </li>
      <li>
        <svg viewBox="0 0 16 16"><path d="M8 0a5.5 5.5 0 0 0-5.5 5.5C2.5 10 8 16 8 16s5.5-6 5.5-10.5A5.5 5.5 0 0 0 8 0zm0 3a2.5 2.5 0 1 1 0 5 2.5 2.5 0 0 1 0-5z"/></svg>
        18761 52nd Avenue S,<br>Kent, WA 98047
      </li>
      <li>
        <svg viewBox="0 0 16 16"><path d="M8 1a7 7 0 1 0 0 14A7 7 0 0 0 8 1zm-.7 1.6v3.7H4.8c.2-1.8 1.1-3.3 2.5-3.7zm1.4 0c1.4.4 2.3 1.9 2.5 3.7H8.7zM2.6 7.7h2.2c0 .2 0 .4 0 .6H2.6zm2.2 2h2.5v3.7c-1.4-.4-2.3-1.9-2.5-3.7zm3.9 0h2.5c-.2 1.8-1.1 3.3-2.5 3.7zM7.3 7.7v.6H6.2v-.6zm2.5 0v.6H8.7v-.6zm1.4 0h2.2v.6h-2.2z"/></svg>
        www.varkoworks.com
      </li>
    </ul>
  </div>
</section>

</body>
</html>
```